Facebook Header Design Project.

I'm supplying white and colored logos. The Facebook page already exists. URL = https://www.brindlepost.example/quillarc.studio The design should not be based on what's already there. Consider mobile implications of the design. This Design will form the designs of other social media headers. QuillArc is a web design | digital marketing company.

Target Market(s)

People interested in web design | digital marketing services.

Industry/Entity Type

QuillArc is a web design | digital marketing company. That should be clear in the design.

Colors
0054AA
0677BA
7BADD7
CADEEF
E8F1F8

Requirements
Must have
• Logo. Use Facebook header image dimension.
Nice to have
• Use a color scheme like the logo and feel free to add a color or two from the other side of the color whee.

```html
<!DOCTYPE html>
<html lang="en">
<head>
<meta charset="utf-8">
<title>QuillArc – Social Header</title>
<link rel="stylesheet" href="https://fonts.googleapis.com/css2?family=Exo+2:ital,wght@1,600&family=Montserrat:wght@600;700&display=swap">
<style>
  :root {
    --navy: #2c4f9e;
    --brand-blue: #2b5aa5;
    --deep-blue: #0677ba;
    --mid-blue: #3b8cc8;
    --sky: #7badd7;
    --mist: #cadeef;
    --ice: #e8f1f8;
    --paper: #ffffff;
  }
  * { box-sizing: border-box; margin: 0; padding: 0; }
  html, body {
    width: 1200px;
    height: 457px;
    overflow: hidden;
    background: var(--paper);
  }
  .header-canvas {
    position: relative;
    width: 1200px;
    height: 457px;
    overflow: hidden;
    background: var(--paper);
  }
  .corner-wave {
    position: absolute;
    filter: drop-shadow(0 0 6px rgba(43, 90, 165, 0.18));
  }
  .corner-wave--top-left { left: 0; top: 0; }
  .corner-wave--bottom-right { right: 0; bottom: 0; }

  .content-frame {
    position: absolute;
    left: 50px;
    top: 47px;
    width: 1097px;
    height: 366px;
    border: 1.5px solid var(--navy);
    border-radius: 10px;
    background: rgba(255, 255, 255, 0.55);
    box-shadow: 0 0 8px rgba(43, 90, 165, 0.15);
  }

  .brand-name {
    position: absolute;
    left: 0;
    width: 1200px;
    top: 112px;
    text-align: center;
    font-family: "Montserrat", sans-serif;
    font-weight: 700;
    font-size: 84px;
    line-height: 1;
    letter-spacing: 0.01em;
    color: var(--brand-blue);
  }

  .tagline {
    position: absolute;
    left: 0;
    width: 1200px;
    top: 274px;
    text-align: center;
    font-family: "Montserrat", sans-serif;
    font-weight: 600;
    font-size: 15px;
    letter-spacing: 0.62em;
    padding-left: 0.62em;
    color: var(--navy);
  }

  .service-track {
    position: absolute;
    left: 200px;
    top: 328px;
    width: 782px;
    height: 2px;
    background: linear-gradient(90deg, var(--deep-blue), var(--sky) 70%, var(--mist));
  }
  .service-dot {
    position: absolute;
    top: 321px;
    width: 16px;
    height: 16px;
    margin-left: -8px;
    border-radius: 50%;
    background: radial-gradient(circle at 70% 35%, var(--ice) 0%, var(--sky) 45%, var(--deep-blue) 100%);
  }
  .service-label {
    position: absolute;
    top: 352px;
    width: 240px;
    margin-left: -120px;
    text-align: center;
    font-family: "Exo 2", sans-serif;
    font-style: italic;
    font-weight: 600;
    font-size: 14px;
    color: var(--navy);
    white-space: nowrap;
  }
</style>
</head>
<body>
  <main class="header-canvas">
    <svg class="corner-wave corner-wave--top-left" width="262" height="222" viewBox="0 0 262 222" aria-hidden="true">
      <defs>
        <linearGradient id="waveTopLeft" x1="0" y1="0" x2="1" y2="0">
          <stop offset="0" stop-color="#2d88c5"/>
          <stop offset="0.55" stop-color="#7badd7"/>
          <stop offset="1" stop-color="#cadeef"/>
        </linearGradient>
      </defs>
      <path d="M0 0 H238 C262 20 262 60 236 72 C200 88 120 80 96 118 C78 146 92 200 0 216 Z" fill="url(#waveTopLeft)"/>
    </svg>

    <svg class="corner-wave corner-wave--bottom-right" width="280" height="175" viewBox="0 0 280 175" aria-hidden="true">
      <defs>
        <linearGradient id="waveBottomRight" x1="0" y1="0" x2="1" y2="0">
          <stop offset="0" stop-color="#0677ba"/>
          <stop offset="0.5" stop-color="#7badd7"/>
          <stop offset="1" stop-color="#cadeef"/>
        </linearGradient>
      </defs>
      <path d="M280 8 C240 -6 186 10 170 52 C160 80 150 96 110 98 C50 100 12 130 8 175 H280 Z" fill="url(#waveBottomRight)"/>
    </svg>

    <div class="content-frame"></div>

    <h1 class="brand-name">QuillArc</h1>
    <p class="tagline">DIGITAL MARKETING COMPANY</p>

    <div class="service-track"></div>
    <span class="service-dot" style="left:200px"></span>
    <span class="service-dot" style="left:376px"></span>
    <span class="service-dot" style="left:598px"></span>
    <span class="service-dot" style="left:814px"></span>
    <span class="service-dot" style="left:982px"></span>

    <p class="service-label" style="left:200px">Website Design</p>
    <p class="service-label" style="left:377px">Website Development</p>
    <p class="service-label" style="left:598px">Search Engine Optimization</p>
    <p class="service-label" style="left:816px">Digital Marketing</p>
    <p class="service-label" style="left:983px">Graphic Design</p>
  </main>
</body>
</html>
```